Brook Refrigeration. Refrigeration and air conditioning specialists.

We need a website to promote our business. We would a modern simple design using the colours from our logo and black. We want it to be fun but proffesional.

Target Market(s)

Commercial

Number of Pages Required

4 page

Requirements
Must have
• Home Page, About Us, Services and Contact Us.
• 24/7 365 days service available.
• Brook Refrigeration's dedicated team specialises in commercial refrigeration and air conditioning equipment.
• Based in Joondalup, we cover Perth Metro and surrounding areas.
Nice to have
• KNOWLEDGE . EXPERIENCE . PASSION in bold.
• Our experienced and highly trained technicians provide extensive knowledge and exceptional skills for your commercial refrigeration and air conditioning requirements.
• Pictures of commercial refrigeration.
Should not have
• No mention of domestic services.

```html
<!DOCTYPE html>
<html lang="en">
<head>
<meta charset="utf-8">
<title>Brook Refrigeration</title>
<link href="https://fonts.googleapis.com/css2?family=Jost:wght@400;500;600&family=Montserrat:wght@500;600;700;800&family=Roboto:wght@400;500;700&display=swap" rel="stylesheet">
<style>
:root{
  --purple:#3f2868;
  --purple-dark:#2e1b4f;
  --green:#a8e85c;
  --green-dark:#8ccf3e;
  --ink:#333;
  --grey:#777;
  --line:#d6d6d6;
  --footer:#333333;
}
*{box-sizing:border-box;margin:0;padding:0}
html,body{width:1200px;height:3629px;overflow:hidden}
body{position:relative;font-family:"Roboto",sans-serif;color:var(--ink);background:#fff}
a{text-decoration:none}

/* header */
.header{position:absolute;left:0;top:0;width:1200px;height:145px;background:#fff}
.phone-tab{position:absolute;left:907px;top:0;width:293px;height:44px;background:var(--green);border-bottom-left-radius:30px;display:flex;align-items:center;padding-left:22px;gap:12px;font:700 22px "Roboto",sans-serif;color:var(--purple)}
.brand{position:absolute;left:85px;top:52px;font:700 26px/32px "Montserrat",sans-serif;color:var(--purple)}
.availability{position:absolute;left:700px;top:28px;text-align:center;color:var(--purple)}
.availability .dot{width:46px;height:46px;border-radius:50%;border:5px solid var(--purple);margin:0 auto 4px}
.availability .big{font:800 26px "Montserrat",sans-serif}
.availability .big span{font-size:19px}
.availability small{display:block;font-size:8px;font-weight:700;letter-spacing:.5px;margin-top:-2px}
.follow{position:absolute;left:945px;top:56px;text-align:center;width:140px}
.follow h4{font:700 20px "Roboto",sans-serif;color:var(--purple);margin-bottom:6px}
.follow .squares{display:flex;gap:3px;justify-content:center}
.follow .squares i{width:18px;height:18px;background:var(--purple);display:block}
.follow .squares i:nth-child(even){background:#5a7bb5}

/* nav */
.nav{position:absolute;left:0;top:145px;width:1200px;height:35px;background:var(--purple)}
.nav a{position:absolute;top:0;height:35px;line-height:35px;font-size:14px;color:#fff;text-align:center}
.nav .active{left:85px;width:137px;background:var(--green);color:var(--purple)}
.nav .sep{position:absolute;top:4px;width:1px;height:27px;background:#5c4684}
.search{position:absolute;left:925px;top:6px;width:185px;height:23px;background:#fff;font-size:11px;color:var(--grey);padding:5px 8px}
.search svg{position:absolute;right:7px;top:5px}

/* hero */
.hero{position:absolute;left:0;top:180px;width:1200px;height:662px;background:linear-gradient(90deg,#3a3d42 0%,#5d6168 40%,#7a8594 70%,#2d3a5a 100%)}
.hero-text{position:absolute;left:103px;top:216px;width:580px;text-align:center;color:#fff}
.hero-text .lead{font:400 31px "Jost",sans-serif}
.hero-text h1{font:500 34px/44px "Jost",sans-serif;margin-top:8px;letter-spacing:.5px}
.hero-text .tag{font:600 24px "Jost",sans-serif;color:var(--green);margin-top:8px;letter-spacing:2px}
.dots{position:absolute;left:385px;top:573px;display:flex;gap:10px}
.dots i{width:9px;height:9px;border-radius:50%;border:1.5px solid #fff;display:block}
.dots i:first-child{background:#fff}

/* about + contact */
.section-title{font:700 32px "Montserrat",sans-serif;color:var(--purple)}
.about{position:absolute;left:109px;top:920px;width:508px}
.title-rule{height:1px;background:var(--line);margin-top:12px}
.about-photo{width:508px;height:227px;margin-top:20px;background:linear-gradient(135deg,#5c5f66,#a33a3a 55%,#d9cbbd)}
.about p{font-size:11.5px;line-height:20px;color:var(--grey);margin-top:26px}
.about p + p{margin-top:16px}
.btn{display:inline-block;background:var(--purple);color:#fff;font:500 11px "Roboto",sans-serif;text-align:center;height:29px;line-height:29px;width:123px}
.about .btn{position:absolute;left:0;top:566px}
.contact{position:absolute;left:690px;top:920px;width:455px}
.field{margin-top:20px}
.field:first-of-type{margin-top:22px}
.field label{font-size:11px;color:var(--grey);display:block;margin-bottom:8px}
.field label b{color:var(--purple)}
.field .box{width:402px;height:36px;border:1px solid var(--line);background:#f7f7f7;margin-left:5px}
.field .area{height:100px}
.req{font-size:11px;color:var(--grey);margin-top:12px}
.agree{font-size:11.5px;color:var(--grey);margin-top:26px;display:flex;align-items:center;gap:10px}
.agree i{width:14px;height:14px;border:1px solid #bbb;display:block}
.contact .btn{position:absolute;left:5px;top:566px}

/* services */
.services{position:absolute;left:0;top:1626px;width:1200px;height:934px;background:linear-gradient(180deg,#4a2f78 0%,#5b3f8a 45%,#4b3079 100%)}
.services h2{position:absolute;top:76px;width:1200px;text-align:center;font:600 28px "Montserrat",sans-serif;color:#fff}
.services .rule{position:absolute;left:568px;top:124px;width:64px;height:2px;background:#fff}
.services .intro{position:absolute;top:155px;left:120px;width:960px;text-align:center;font-size:12px;line-height:25px;color:#e4dcf0}
.card{position:absolute;width:254px;height:252px;border:2px solid #e8e2f2;text-align:center;color:#fff}
.card .num{width:48px;height:48px;background:var(--green);margin:50px auto 0;font:500 30px/48px "Montserrat",sans-serif;color:#fff}
.card h3{font:700 15px "Montserrat",sans-serif;margin-top:16px}
.card p{font-size:11.5px;line-height:17px;color:#e4dcf0;margin:14px auto 0;width:190px}

/* testimonials */
.testimonials h2{position:absolute;top:2655px;width:1200px;text-align:center;font:700 30px "Montserrat",sans-serif;color:var(--purple)}
.testimonials .rule{position:absolute;left:540px;top:2708px;width:120px;height:1px;background:var(--line)}
.quote{position:absolute;top:2766px;width:380px;height:128px;border:1.5px solid #9a9a9a;padding:26px 24px}
.quote .mark{position:absolute;left:20px;top:-24px;font:700 42px "Montserrat",sans-serif;color:var(--green);background:#fff;padding:0 3px;line-height:40px}
.quote h4{font:700 13px "Roboto",sans-serif;color:var(--purple)}
.quote p{font-size:11.5px;line-height:17px;color:var(--purple);margin-top:8px}
.quote .tail{position:absolute;left:26px;bottom:-12px;width:22px;height:22px;background:#fff;border-right:1.5px solid #9a9a9a;border-bottom:1.5px solid #9a9a9a;transform:rotate(45deg)}
.person{position:absolute;top:2912px;display:flex;align-items:center;gap:10px}
.person .avatar{width:42px;height:42px;border-radius:50%;background:linear-gradient(135deg,#c9b6a5,#6d5a4d)}
.person b{font:700 12px "Roboto",sans-serif;color:var(--purple);display:block}
.person small{font-size:9px;color:var(--grey)}

/* newsletter */
.newsletter{position:absolute;left:0;top:3080px;width:1200px;height:153px;background:var(--green)}
.newsletter h3{position:absolute;left:174px;top:64px;font:700 23px "Montserrat",sans-serif;color:var(--purple);letter-spacing:.5px}
.newsletter .input{position:absolute;left:382px;top:54px;width:506px;height:51px;background:#fff}
.newsletter .submit{position:absolute;left:888px;top:54px;width:128px;height:51px;background:var(--purple);color:#fff;font:700 14px/51px "Roboto",sans-serif;text-align:center}

/* footer */
.footer{position:absolute;left:0;top:3233px;width:1200px;height:324px;background:var(--footer);color:#fff}
.footer-brand{position:absolute;left:109px;top:118px;width:200px;font:700 22px/30px "Montserrat",sans-serif;color:#fff}
.fcol{position:absolute;top:73px}
.fcol h4{font:700 16px "Montserrat",sans-serif;color:var(--green);letter-spacing:.5px}
.fitem{display:flex;gap:14px;margin-top:26px}
.fitem b{display:block;color:var(--green);font-size:14px}
.fitem span{font-size:14px;line-height:18px}
.links a{display:block;color:#fff;font-size:14px;margin-top:18px}
.links a:first-of-type{margin-top:32px}
.finput{position:absolute;background:#fff;height:37px;color:#999;font-size:12px;padding:11px 12px}
.send{position:absolute;left:794px;top:203px;width:130px;height:39px;background:var(--green);color:var(--purple);font:700 15px/39px "Roboto",sans-serif;text-align:center}
.bottom{position:absolute;left:0;top:3557px;width:1200px;height:72px;background:var(--purple);color:#cfc6df;font-size:12px;text-align:center;line-height:72px}
</style>
</head>
<body>

<header class="header">
  <div class="phone-tab">
    <svg width="26" height="26" viewBox="0 0 26 26"><rect x="7" y="2" width="12" height="22" rx="2" fill="none" stroke="#3f2868" stroke-width="2.5"/><path d="M3 8q-2 5 0 10M23 8q2 5 0 10" fill="none" stroke="#3f2868" stroke-width="2"/></svg>
    1-800-555-0142
  </div>
  <div class="brand">Brook Refrigeration</div>
  <div class="availability"><div class="dot"></div><div class="big">24/7 <span>365 DAYS</span></div><small>SERVICE AVAILABLE</small></div>
  <div class="follow"><h4>Follow Us</h4><div class="squares"><i></i><i></i><i></i><i></i><i></i><i></i></div></div>
</header>

<nav class="nav">
  <a class="active" href="#">Home</a>
  <span class="sep" style="left:222px"></span>
  <a href="#" style="left:222px;width:200px">About Us</a>
  <span class="sep" style="left:422px"></span>
  <a href="#" style="left:422px;width:176px">Services</a>
  <span class="sep" style="left:598px"></span>
  <a href="#" style="left:598px;width:210px">Contact Us</a>
  <span class="sep" style="left:808px"></span>
  <div class="search">Search
    <svg width="12" height="12" viewBox="0 0 12 12"><circle cx="5" cy="5" r="3.5" fill="none" stroke="#555" stroke-width="1.5"/><path d="M7.5 7.5L11 11" stroke="#555" stroke-width="1.5"/></svg>
  </div>
</nav>

<section class="hero" role="img" aria-label="Photo of commercial condenser fans with a smiling technician in uniform holding a clipboard">
  <div class="hero-text">
    <div class="lead">Our dedicated team specialises in</div>
    <h1>COMMERCIAL REFRIGERATION &amp;<br>AIR CONDITIONING EQUIPMENT.</h1>
    <div class="tag">KNOWLEDGE • EXPERIENCE • PASSION</div>
  </div>
  <div class="dots"><i></i><i></i><i></i></div>
</section>

<section class="about">
  <h2 class="section-title">About us</h2>
  <div class="title-rule"></div>
  <div class="about-photo" role="img" aria-label="Photo of a technician wiring a refrigeration unit"></div>
  <p>Brook Refrigeration's dedicated team specialises in commercial refrigeration and air conditioning equipment. Based in Joondalup, we cover Perth Metro and surrounding areas.</p>
  <p>Lorem ipsum dolor sit amet, consectetur adipiscing elit. Morbi auctor ullamcorper congue. Phasellus quis lacus quis ante ornare tincidunt lobortis quis enim. Nam lacinia ex ac quam sollicitudin placerat. Nullam eu laoreet diam. Vivamus sed mattis est. Cras fringilla maximus magna, eleifend pellentesque tellus volutpat eu. Sed sed ornare dolor, quis tempor justo. Curabitur at turpis justo. Curabitur sem sapien, vulputate sed efficitur. Lorem ipsum dolor sit amet, consectetur adipiscing elit. Morbi auctor ullamcorper congue. Phasellus quis lacus quis ante ornare tincidunt lobortis quis enim.</p>
  <a class="btn" href="#">READ MORE</a>
</section>

<section class="contact">
  <h2 class="section-title">Contact Us</h2>
  <div class="title-rule"></div>
  <div class="field"><label>NAME <b>*</b></label><div class="box"></div></div>
  <div class="field"><label>EMAIL <b>*</b></label><div class="box"></div></div>
  <div class="field"><label>PHONE</label><div class="box"></div></div>
  <div class="field"><label>DESCRIPTION</label><div class="box area"></div></div>
  <div class="req">• Required</div>
  <div class="agree"><i></i>I have read the Disclaimer and Privacy Policy</div>
  <a class="btn" href="#">READ MORE</a>
</section>

<section class="services" role="img" aria-label="Purple-tinted photo of refrigeration pipework behind the services list">
  <h2>Our Services</h2>
  <div class="rule"></div>
  <p class="intro">Whether you wish to cool, store or display food and drink, we have a wide range of commercial refrigerator services catering to various small and large scale industries.<br>We specialize in wide range of commercial refrigeration operations and maintenance services to ensure efficient functioning of the systems.</p>
  <div class="card" style="left:149px;top:259px"><div class="num">01</div><h3>Commercial Freezer</h3><p>Lorem ipsum dolor sit amet, consectetur adipiscing elit. Morbi auctor ullamcorper congue.</p></div>
  <div class="card" style="left:473px;top:259px"><div class="num">02</div><h3>Walk In Cooler</h3><p>Lorem ipsum dolor sit amet, consectetur adipiscing elit. Morbi auctor ullamcorper congue.</p></div>
  <div class="card" style="left:797px;top:259px"><div class="num">03</div><h3>Kitchen Refrigeration</h3><p>Lorem ipsum dolor sit amet, consectetur adipiscing elit. Morbi auctor ullamcorper congue.</p></div>
  <div class="card" style="left:149px;top:576px"><div class="num">04</div><h3>Glass Door Merchandiser</h3><p>Lorem ipsum dolor sit amet, consectetur adipiscing elit. Morbi auctor ullamcorper congue.</p></div>
  <div class="card" style="left:473px;top:576px"><div class="num">05</div><h3>Commercial Freezer</h3><p>Lorem ipsum dolor sit amet, consectetur adipiscing elit. Morbi auctor ullamcorper congue.</p></div>
  <div class="card" style="left:797px;top:576px"><div class="num">06</div><h3>Ice machines</h3><p>Lorem ipsum dolor sit amet, consectetur adipiscing elit. Morbi auctor ullamcorper congue.</p></div>
</section>

<section class="testimonials">
  <h2>Client Testimonials</h2>
  <div class="rule"></div>
  <div class="quote" style="left:189px"><span class="mark">“</span><h4>Lorem ipsum dolor</h4><p>Lorem ipsum dolor sit amet, consectetur adipiscing elit. Quid autem habent admirationis, cum prope accesseris? An hoc usque quaque, aliter in vita?</p><span class="tail"></span></div>
  <div class="person" style="left:209px"><div class="avatar" role="img" aria-label="Client portrait"></div><div><b>MARA ELLISON</b><small>Lorem ipsum dolor</small></div></div>
  <div class="quote" style="left:632px"><span class="mark">“</span><h4>Lorem ipsum dolor</h4><p>Lorem ipsum dolor sit amet, consectetur adipiscing elit. Quid autem habent admirationis, cum prope accesseris? An hoc usque quaque, aliter in vita?</p><span class="tail"></span></div>
  <div class="person" style="left:650px"><div class="avatar" role="img" aria-label="Client portrait"></div><div><b>TOM REYES</b><small>Lorem ipsum</small></div></div>
</section>

<section class="newsletter">
  <h3>NEWSLETTER</h3>
  <div class="input"></div>
  <div class="submit">SUBSCRIBE</div>
</section>

<footer class="footer">
  <div class="footer-brand">Brook Refrigeration</div>
  <div class="fcol" style="left:358px">
    <h4>CONTACT US</h4>
    <div class="fitem">
      <svg width="22" height="30" viewBox="0 0 22 30"><path d="M11 1C5 1 1 5.5 1 11c0 8 10 18 10 18s10-10 10-18C21 5.5 17 1 11 1z" fill="#a8e85c"/><circle cx="11" cy="11" r="4" fill="#333"/></svg>
      <div><b>ADDRESS</b><span>14 Harbour Way<br>Joondalup, WA 6027</span></div>
    </div>
    <div class="fitem">
      <svg width="22" height="22" viewBox="0 0 24 24"><path d="M6.6 10.8a15 15 0 0 0 6.6 6.6l2.2-2.2c.3-.3.7-.4 1-.2 1.1.4 2.3.6 3.6.6.6 0 1 .4 1 1V20c0 .6-.4 1-1 1A17 17 0 0 1 3 4c0-.6.4-1 1-1h3.5c.6 0 1 .4 1 1 0 1.3.2 2.5.6 3.6.1.3 0 .7-.2 1z" fill="#a8e85c"/></svg>
      <div><b>PHONE NUMBER</b><span>1-800-555-0142</span></div>
    </div>
  </div>
  <div class="fcol links" style="left:624px">
    <h4>ABOUT</h4>
    <a href="#">Home</a><a href="#">About Us</a><a href="#">Services</a><a href="#">Contact us</a>
  </div>
  <div class="fcol" style="left:789px"><h4>GET IN TOUCH</h4></div>
  <div class="finput" style="left:794px;top:114px;width:152px">Name</div>
  <div class="finput" style="left:951px;top:114px;width:153px">Phone</div>
  <div class="finput" style="left:794px;top:157px;width:310px">Email address</div>
  <div class="send">SEND</div>
</footer>

<div class="bottom">© 2018 brookrefrigeration All Right Reserved</div>

</body>
</html>
```